2 sided Handyman Postcard Design with coupon on the back

Company name is "Marlo QuickFix" Looking for a postcard that's also a business card. Showing Marlo QuickFix, 4817 Dunmore Hollow Rd NE, Brindle Falls, Ohio 43977, 740-318-6642, mtwelbeck@quillpost.example coupon- $25 off any job over $100, $50 off any job over $250, $75 off any job over $500, $100 off any job over $750, qualifications, experience 25 years. No job is to small. Handyman service. home repair. Free estimates. Examples, Flooring, Cabinets, Decks, Odd Jobs, Carpentry, Painting, Drywall repair, Ceramic tile, Screen repair, fence repair, Pressure wash, Hang a Picture, wood rot repair, Plumbing, Electrical, Small Jobs, Install ceiling fan, replace garbage disposal, toilet repair, install new lighting, Install safety grab bars, caulk tub or Kitchen, Hang Blinds/rods, Replace a switch/outlet, Replace/adjust doors and locksets, replace faucets/sinks/vanity tops, And much more. Have a signature look, I wear a aussie breezier hat on the job, full beard, and glasses. Am looking for a caricature of that with tools as main logo which should be shown on front and the back. One year warranty, Bonded, Insured. Cash or checks

```html
<!DOCTYPE html>
<html lang="en">
<head>
<meta charset="utf-8">
<title>Marlo QuickFix – Handyman Postcard</title>
<link href="https://fonts.googleapis.com/css2?family=Merriweather:wght@400;900&family=Oswald:wght@600;700&family=Roboto:wght@400;700;900&display=swap" rel="stylesheet">
<style>
  :root{
    --stage:#2c2c2c;
    --navy:#233f8a;
    --navy-deep:#1c3275;
    --orange:#f0561f;
    --orange-light:#f77f2a;
    --red:#e4232b;
    --yellow:#f3e45c;
    --swoosh:#aebbe0;
    --white:#ffffff;
    --paper:#fbfbf9;
    --ink:#111111;
    --grey:#8a8a8a;
  }
  *{margin:0;padding:0;box-sizing:border-box}
  html,body{width:1200px;height:943px;overflow:hidden;background:var(--stage)}
  body{position:relative;font-family:"Roboto",Arial,sans-serif}

  .card{position:absolute;left:253px;width:604px;overflow:hidden}
  .card-front{top:5px;height:448px;background:var(--navy)}
  .card-back{top:463px;height:470px;background:var(--paper)}
  .abs{position:absolute}
  .bg{position:absolute;left:0;top:0}

  .mascot{position:absolute;border-radius:40% 40% 12% 12%;
    background:linear-gradient(180deg,#6b4a2c 0%,#e6b58a 22%,#3a6fc4 45%,#2a55a8 80%,#6a4a30 100%)}

  .brand-name{font-family:"Merriweather",Georgia,serif;font-weight:900;color:var(--white);letter-spacing:.5px;white-space:nowrap}
  .brand-tag{font-family:"Merriweather",Georgia,serif;color:var(--yellow);font-size:19px}

  .badge{position:absolute;left:447px;top:16px;width:128px;height:126px}
  .badge-text{position:absolute;left:0;top:36px;width:128px;text-align:center;transform:rotate(-12deg);color:var(--white);font-family:"Oswald",Impact,sans-serif;font-weight:700;line-height:1}
  .badge-text .big{font-size:30px;letter-spacing:1px;display:block}
  .badge-text .small{font-size:14px;display:block;margin-top:2px}

  .services-title{left:190px;top:122px;color:var(--orange-light);font-weight:700;font-size:20px;letter-spacing:.4px;line-height:22px}
  .services{top:146px;list-style:none;color:var(--white);font-weight:700;font-size:10.6px;line-height:13.8px}
  .services li::before{content:"▪";font-size:7px;margin-right:2px;vertical-align:2px}
  .col1{left:190px}.col2{left:276px}.col3{left:395px}

  .slogan{left:271px;top:283px;font-family:"Merriweather",Georgia,serif;font-weight:900;color:var(--white);font-size:19px;letter-spacing:.2px}
  .call{font-family:"Oswald",Impact,sans-serif;font-weight:700;color:var(--orange-light);letter-spacing:-.5px;white-space:nowrap}
  .call-front{left:254px;top:302px;font-size:30px;display:flex;align-items:center;gap:4px}

  .address-label{left:39px;top:376px;font-size:15px;color:var(--ink)}
  .address{left:39px;top:393px;font-size:15px;font-weight:700;color:var(--white);line-height:17px}
  .email-front{left:342px;top:408px;font-size:16px;color:var(--white);display:flex;align-items:center;gap:7px}

  .back-name{left:115px;top:30px;font-size:25px}
  .back-address{left:115px;top:60px;font-size:10.5px;font-weight:700;color:var(--white);white-space:nowrap}
  .qualify{left:144px;top:117px;color:var(--white);font-size:18px;line-height:19px;letter-spacing:.2px}

  .coupons{left:34px;top:170px;width:240px;height:157px;background:var(--white);border:1.5px dashed #555;display:grid;grid-template-columns:1fr 1fr;grid-template-rows:1fr 1fr}
  .coupon{border:1px dashed #555;padding:8px 3px 0 6px}
  .coupon-amount{display:flex;align-items:flex-start;color:var(--red);font-family:"Roboto",Arial,sans-serif;font-weight:900;line-height:1}
  .coupon-amount .num{font-size:37px;letter-spacing:-1px}
  .coupon-amount .unit{display:flex;flex-direction:column;margin-top:3px}
  .coupon-amount .dollar{font-size:10px;color:var(--ink)}
  .coupon-amount .off{font-size:19px;font-weight:400;color:var(--ink);margin-top:-2px}
  .coupon-term{margin-top:3px;background:var(--navy);color:var(--white);font-size:10.5px;text-align:center;padding:1px 0;width:104px}
  .call-back{left:46px;top:329px;font-size:25px;line-height:32px}
  .email-back{left:38px;top:363px;font-size:12.5px;color:var(--white);white-space:nowrap;line-height:15px}

  .stamp{left:507px;top:29px;width:69px;height:78px;border:1px solid #aaa;background:var(--white);color:var(--grey);font-size:12px;line-height:15px;padding:18px 0 0 17px}
  .address-line{left:339px;width:212px;height:1px;background:#777}
</style>
</head>
<body>

<section class="card card-front" aria-label="Postcard front">
  <svg class="bg" width="604" height="448" viewBox="0 0 604 448">
    <defs>
      <linearGradient id="orangeBand" x1="0" y1="0" x2="1" y2="0">
        <stop offset="0" stop-color="#f04e1c"/><stop offset="1" stop-color="#ee5a22"/>
      </linearGradient>
    </defs>
    <path d="M0 275 C120 300 220 330 330 345 C440 360 540 360 604 352 L604 448 L0 448 Z" fill="#fff"/>
    <path d="M0 290 C120 312 220 345 330 358 C440 372 540 372 604 366 L604 448 L0 448 Z" fill="url(#orangeBand)"/>
    <path d="M150 150 C170 110 280 100 430 105 C350 100 220 110 165 150 Z" fill="var(--swoosh)"/>
    <path d="M255 318 C240 350 380 352 520 338 C590 328 600 308 565 298 C580 318 520 335 380 340 C300 342 255 338 255 318 Z" fill="var(--swoosh)"/>
  </svg>

  <div class="mascot" style="left:38px;top:22px;width:150px;height:325px" role="img" aria-label="Caricature mascot of the handyman in a brimmed hat, beard and glasses, overalls, giving a thumbs up and holding a red toolbox"></div>

  <h1 class="brand-name abs" style="left:155px;top:34px;font-size:27px">MARLO QUICKFIX</h1>
  <p class="brand-tag abs" style="left:157px;top:66px">Handyman Service</p>

  <div class="badge">
    <svg width="128" height="126" viewBox="0 0 128 126">
      <polygon fill="var(--red)" points="64,2 74,20 94,8 96,30 120,26 110,46 126,60 108,72 120,92 96,92 94,116 74,104 64,124 54,104 34,116 32,92 8,92 20,72 2,60 18,46 8,26 32,30 34,8 54,20"/>
    </svg>
    <div class="badge-text"><span class="big">FREE</span><span class="small">ESTIMATES</span></div>
  </div>

  <h2 class="services-title abs">SERVICES INCLUDES</h2>
  <ul class="services col1 abs">
    <li>Flooring,</li><li>Cabinets,</li><li>Decks,</li><li>Odd Jobs,</li><li>Carpentry,</li><li>Painting,</li><li>Drywall repair,</li><li>Ceramic tile,</li>
  </ul>
  <ul class="services col2 abs">
    <li>Screen repair,</li><li>Fence repair,</li><li>Pressure wash,</li><li>Hang a Picture,</li><li>Wood rot repair,</li><li>Plumbing, Electrical,</li><li>Small Jobs,</li><li>Install ceiling fan,</li><li>Toilet repair,</li>
  </ul>
  <ul class="services col3 abs">
    <li>Replace garbage disposal,</li><li>Install new lighting,</li><li>Install safety grab bars,</li><li>Caulk tub or Kitchen,</li><li>Hang Blinds/rods,</li><li>Replace a switch/outlet,</li><li>Replace/adjust doors and locksets,</li><li>Replace faucets/sinks/vanity tops,</li><li>And much more</li>
  </ul>

  <p class="slogan abs">NO JOB IS TOO SMALL</p>
  <p class="call call-front abs">
    <svg width="16" height="26" viewBox="0 0 16 26" aria-hidden="true"><path d="M5 1 L9 1 L9 7 L6 8 C5 12 5 15 6 18 L9 19 L9 25 L5 25 C0 20 0 6 5 1 Z" fill="#fff"/></svg>
    CALL - 740-318-6642
  </p>

  <p class="address-label abs">Address</p>
  <p class="address abs">4817 Dunmore Hollow Rd NE,<br>Brindle Falls, Ohio 43977</p>
  <p class="email-front abs">
    <svg width="24" height="16" viewBox="0 0 24 16" aria-hidden="true"><rect x="1" y="1" width="22" height="14" fill="none" stroke="#111" stroke-width="1.6"/><path d="M1 1 L12 9 L23 1" fill="none" stroke="#111" stroke-width="1.6"/></svg>
    mtwelbeck@quillpost.example
  </p>
</section>

<section class="card card-back" aria-label="Postcard back">
  <svg class="bg" width="604" height="470" viewBox="0 0 604 470">
    <path d="M0 0 H454 V150 H292 V382 H0 Z" fill="var(--navy)"/>
    <path d="M120 150 C110 120 200 108 340 108 C230 112 150 125 140 150 Z" fill="var(--swoosh)"/>
  </svg>

  <div class="mascot" style="left:34px;top:20px;width:70px;height:125px" role="img" aria-label="Small caricature mascot of the handyman in a brimmed hat with beard and glasses, holding a red toolbox"></div>

  <h1 class="brand-name back-name abs">MARLO QUICKFIX</h1>
  <p class="back-address abs">4817 Dunmore Hollow Rd NE, Brindle Falls, Ohio 43977</p>
  <p class="qualify abs">QUALIFICATIONS, EXPERIENCE<br>25 YEARS</p>

  <div class="coupons abs">
    <div class="coupon"><div class="coupon-amount"><span class="num">25</span><span class="unit"><span class="dollar">$</span><span class="off">OFF</span></span></div><p class="coupon-term">Any Job Over $100</p></div>
    <div class="coupon"><div class="coupon-amount"><span class="num">50</span><span class="unit"><span class="dollar">$</span><span class="off">OFF</span></span></div><p class="coupon-term">Any Job Over $250</p></div>
    <div class="coupon"><div class="coupon-amount"><span class="num">75</span><span class="unit"><span class="dollar">$</span><span class="off">OFF</span></span></div><p class="coupon-term">Any Job Over $500</p></div>
    <div class="coupon" style="padding-left:2px"><div class="coupon-amount"><span class="num">100</span><span class="unit"><span class="dollar">$</span><span class="off">OFF</span></span></div><p class="coupon-term">Any Job Over $750</p></div>
  </div>

  <p class="call call-back abs">CALL - 740-318-6642</p>
  <p class="email-back abs">Email - mtwelbeck@quillpost.example</p>

  <div class="stamp abs">Place<br>Stamp<br>Here</div>
  <div class="address-line abs" style="top:225px"></div>
  <div class="address-line abs" style="top:267px"></div>
  <div class="address-line abs" style="top:311px"></div>
</section>

</body>
</html>
```